New Graphic Design Project / Email signiture and Letterhead

I would like a new SIMPLE but high end quality modern/heavy industrial design for an email Signiture and letter head that incorporates product photos or illustrations of our products to show our customers our range of products and also show our head office in Perth Western Australia and also our Australian and international reseller locations.
in my present email signature you would see that I have other company logos these companies are old partners of ours but some are no longer so I would like to have the option to add and change them if things change in the future.
for ideas Our main products are as follows
Composite Hose
Convoluted hose
Metal expansion joints
Fabric expansion joints
Rubber Expansion joints
Please see our website for ideas and our product photos.
www.norvaquip.com.au
if you need any further information please let me know
i have attached our old email signiture for reference.
Dale

Target Market(s)

Oil and Gas / Mining / Petroleum and Chemical Refineries, high end engineering

Requirements
Must have
• pictures / photos of our core products and our company capabilities to show our existing and new customers what we can do.
in the email signature - links to company face book and LinkedIn, our website
I would like to have spaces for my company partners logos and need the final file to be in a format for me to change and update all details
All so our Font is Conthrax SB
Nice to have
• the email signature, I would like this to have all the required information ( as per attached present email signature ) but also be informative / marketing to show customers what we do if possible.
the letter head can be based from the same but simple with or without product photos

```html
<!DOCTYPE html>
<html lang="en">
<head>
<meta charset="utf-8">
<title>Norvaquip Letterhead and Email Signature</title>
<link href="https://fonts.googleapis.com/css2?family=Roboto:wght@400;500;700&display=swap" rel="stylesheet">
<style>
  :root{
    --blue:#1f6fb8;
    --ink:#2f2f2f;
    --grey:#6b6b6b;
    --line:#cfcfcf;
    --page:#ffffff;
    --bg:#ffffff;
    --faint:#f1f1f1;
    --badge:#e6e8ea;
  }
  *{box-sizing:border-box;margin:0;padding:0}
  html,body{width:747px;height:1200px;overflow:hidden;background:var(--bg);font-family:"Roboto",Arial,sans-serif;color:var(--ink)}
  .canvas{position:relative;width:747px;height:1200px}

  /* Letterhead */
  .letterhead{position:absolute;left:62px;top:55px;width:624px;height:785px;background:var(--page);
    box-shadow:0 4px 14px rgba(0,0,0,.22);overflow:hidden}
  .letterhead__brand{position:absolute;left:60px;top:24px;display:flex;align-items:center;gap:8px}
  .brand-dot{width:30px;height:30px;border-radius:50%;background:var(--grey);flex:none}
  .brand-name{font-weight:700;font-size:24px;color:var(--ink);letter-spacing:1px;white-space:nowrap}
  .letterhead__rule{position:absolute;left:245px;right:0;top:44px;height:3px;background:var(--line)}
  .letterhead__rule::after{content:"";position:absolute;right:0;top:0;width:190px;height:3px;background:var(--blue)}
  .letterhead__ring{position:absolute;right:-40px;top:300px;width:200px;height:200px;border-radius:50%;
    border:26px solid var(--faint)}
  .letterhead__signoff{position:absolute;left:60px;top:648px;font-size:10px;line-height:14px}
  .letterhead__signoff strong{font-weight:700;font-size:11px}
  .letterhead__signoff span{display:block;color:var(--grey)}
  .letterhead__marker{position:absolute;left:0;top:710px;width:8px;height:22px;background:var(--blue)}
  .letterhead__footer{position:absolute;left:60px;right:30px;top:718px;border-top:1px solid var(--line);
    padding-top:10px;display:flex;justify-content:space-between;font-size:9px;color:var(--grey)}
  .footer-item{display:flex;align-items:center;gap:5px;white-space:nowrap}
  .footer-item svg{width:10px;height:10px;fill:var(--blue);flex:none}
  .letterhead__band{position:absolute;left:0;right:0;bottom:0;height:10px;background:var(--blue)}

  /* Email signature */
  .signature{position:absolute;left:62px;top:905px;width:624px;height:230px;background:var(--page);
    box-shadow:0 4px 14px rgba(0,0,0,.22)}
  .signature__brand{position:absolute;left:26px;top:22px;display:flex;align-items:center;gap:7px}
  .signature__brand .brand-dot{width:28px;height:28px}
  .signature__brand .brand-name{font-size:22px}
  .signature__products{position:absolute;left:26px;top:70px;width:250px;height:40px;border-radius:4px;
    background:linear-gradient(90deg,#8a8f96,#c9ccd0 40%,#6e747b 70%,#b8bcc1)}
  .signature__divider{position:absolute;left:292px;top:20px;width:2px;height:108px;background:var(--grey)}
  .signature__name{position:absolute;left:310px;top:20px;font-size:22px;font-weight:700;color:var(--ink);line-height:24px}
  .signature__title{position:absolute;left:310px;top:46px;font-size:12px;color:var(--grey)}
  .signature__social{position:absolute;right:30px;top:26px;display:flex;gap:6px}
  .signature__social span{width:13px;height:13px;background:var(--grey);border-radius:2px}
  .signature__contacts{position:absolute;left:310px;top:72px;display:grid;grid-template-columns:135px 145px;
    row-gap:5px;font-size:9.5px;color:var(--ink)}
  .signature__contacts .footer-item svg{fill:var(--ink)}
  .signature__countries{position:absolute;left:310px;top:128px;font-size:9.5px;color:var(--grey);
    border-top:1px solid var(--line);padding-top:5px;width:280px;display:flex;justify-content:space-between}
  .signature__countries .sep{color:var(--blue)}
  .signature__partners{position:absolute;left:20px;right:20px;top:160px;display:flex;justify-content:space-between;
    border-top:1px solid var(--line);padding-top:12px}
  .partner-badge{width:52px;height:34px;background:var(--badge);border-radius:3px}
</style>
</head>
<body>
<div class="canvas">

  <section class="letterhead">
    <div class="letterhead__brand"><span class="brand-dot"></span><span class="brand-name">NORVAQUIP</span></div>
    <div class="letterhead__rule"></div>
    <div class="letterhead__ring"></div>

    <div class="letterhead__signoff">
      <strong>Dale Marlow</strong>
      <span>Managing Director</span>
      <span>dale@norvaquip.com.au</span>
    </div>

    <div class="letterhead__marker"></div>
    <div class="letterhead__footer">
      <span class="footer-item"><svg viewBox="0 0 10 10"><path d="M5 0a3.5 3.5 0 0 0-3.5 3.5C1.5 6 5 10 5 10s3.5-4 3.5-6.5A3.5 3.5 0 0 0 5 0zm0 5a1.4 1.4 0 1 1 0-2.8A1.4 1.4 0 0 1 5 5z"/></svg>48 Kestrel Way, Brookdale, WA 6112</span>
      <span class="footer-item"><svg viewBox="0 0 10 10"><path d="M2 0l2 2.5-1 1.2a6 6 0 0 0 3.3 3.3l1.2-1L10 8l-1.5 2C4 10 0 6 0 1.5z"/></svg>+61 8 9000 1234 · +61 8 9000 5678</span>
      <span class="footer-item"><svg viewBox="0 0 10 10"><circle cx="5" cy="5" r="4.5" fill="none" stroke="#1f6fb8" stroke-width="1.2"/><path d="M.5 5h9M5 .5c-2.5 3-2.5 6 0 9M5 .5c2.5 3 2.5 6 0 9" fill="none" stroke="#1f6fb8" stroke-width=".8"/></svg>www.norvaquip.com.au</span>
    </div>
    <div class="letterhead__band"></div>
  </section>

  <section class="signature">
    <div class="signature__brand"><span class="brand-dot"></span><span class="brand-name">NORVAQUIP</span></div>
    <div class="signature__products" role="img" aria-label="Row of product photos: composite hose, convoluted hose and expansion joints"></div>
    <div class="signature__divider"></div>

    <div class="signature__name">Dale Marlow</div>
    <div class="signature__title">Managing Director</div>
    <div class="signature__social"><span></span><span></span><span></span><span></span></div>

    <div class="signature__contacts">
      <span class="footer-item"><svg viewBox="0 0 10 10"><path d="M2 0l2 2.5-1 1.2a6 6 0 0 0 3.3 3.3l1.2-1L10 8l-1.5 2C4 10 0 6 0 1.5z"/></svg>+61 8 9000 1234</span>
      <span class="footer-item"><svg viewBox="0 0 10 10"><circle cx="5" cy="5" r="4.5" fill="none" stroke="#2f2f2f" stroke-width="1.2"/><path d="M.5 5h9M5 .5c-2.5 3-2.5 6 0 9M5 .5c2.5 3 2.5 6 0 9" fill="none" stroke="#2f2f2f" stroke-width=".8"/></svg>www.norvaquip.com.au</span>
      <span class="footer-item"><svg viewBox="0 0 10 10"><path d="M2 0l2 2.5-1 1.2a6 6 0 0 0 3.3 3.3l1.2-1L10 8l-1.5 2C4 10 0 6 0 1.5z"/></svg>+61 8 9000 5678</span>
      <span class="footer-item"><svg viewBox="0 0 10 10"><path d="M5 0a3.5 3.5 0 0 0-3.5 3.5C1.5 6 5 10 5 10s3.5-4 3.5-6.5A3.5 3.5 0 0 0 5 0z"/></svg>48 Kestrel Way</span>
      <span class="footer-item"><svg viewBox="0 0 10 10"><path d="M0 2h10v6H0zM0 2l5 3.5L10 2" fill="none" stroke="#2f2f2f"/></svg>dale@norvaquip.com.au</span>
      <span class="footer-item" style="padding-left:15px">Brookdale, WA 6112</span>
    </div>

    <div class="signature__countries">
      <span>Australia</span><span class="sep">|</span><span>Malaysia</span><span class="sep">|</span><span>Thailand</span><span class="sep">|</span><span>Philippines</span>
    </div>

    <div class="signature__partners">
      <span class="partner-badge"></span><span class="partner-badge"></span><span class="partner-badge"></span>
      <span class="partner-badge"></span><span class="partner-badge"></span><span class="partner-badge"></span>
      <span class="partner-badge"></span><span class="partner-badge"></span><span class="partner-badge"></span>
    </div>
  </section>

</div>
</body>
</html>
```